Tiny Sprout brochure

A brochure or rack card to give expecting parents an idea of the cost savings and enviornmental benefits to cloth diapering their kids. Also let them know its not hard like it was years ago!
Updates

Is anyone working on this? I sent the brief out last week and haven't gotten any submissions. Is my brief lacking information? PLEASE message me if you have questions!

Thanks

Molly

Reason: I have only received one submission!

Target Market(s)

parents

Requirements
Must have
• rack card with front and back OR tri fold brochure

a "why cloth?" section- you don't have to include ALL of the facts I included on my attachment, just a few. I really want to stress the money saved and enviornmenal benefits
pictures/logos of the brands I'm selling
my logo
contact info- www.tinysproutnestling.example and molly@tinysproutnestling.example

a "green" feel, but also want to setress that its not hard like when our parents cloth diapered with safety pins and rubber pants
Should not have
• I

```html
<!DOCTYPE html>
<html lang="en">
<head>
<meta charset="utf-8">
<title>Tiny Sprout – Why Cloth?</title>
<link rel="stylesheet" href="https://fonts.googleapis.com/css2?family=Roboto+Condensed:wght@400;700;800&family=Arimo:wght@400;700&display=swap">
<style>
:root{
  --sky:#cfe6f2;
  --sky-deep:#a9d1e6;
  --leaf:#7cbf3a;
  --leaf-deep:#3f8f2a;
  --leaf-pale:#bfe09a;
  --ink:#2f3a40;
  --blue:#1f6fb6;
  --green-head:#2f7d2a;
  --white:#ffffff;
}
*{box-sizing:border-box;margin:0;padding:0}
html,body{width:1200px;height:2696px;overflow:hidden;background:var(--white)}
.rack-card{position:relative;width:1200px;height:2696px;overflow:hidden;
  background:linear-gradient(180deg,#e4f1f8 0%,var(--sky) 40%,var(--sky-deep) 100%);
  font-family:"Arimo",Arial,sans-serif;color:var(--ink)}
.backdrop{position:absolute;inset:0;width:1200px;height:2696px}
.brand-header{position:absolute;left:0;top:0;width:1200px;height:360px;
  display:flex;flex-direction:column;align-items:center;justify-content:center;gap:12px}
.brand-name{display:flex;align-items:center;gap:24px;
  font-family:"Roboto Condensed",Arial,sans-serif;font-weight:800;font-size:140px;
  color:var(--leaf-deep);letter-spacing:-2px;line-height:1}
.brand-dot{width:80px;height:80px;border-radius:50%;background:var(--leaf)}
.brand-tag{font-family:"Roboto Condensed",Arial,sans-serif;font-weight:700;font-size:38px;
  color:var(--white);background:var(--leaf-deep);padding:6px 44px;border-radius:40px;letter-spacing:3px}
.why-cloth{position:absolute;left:64px;top:375px;width:1072px}
.why-cloth h1{font-family:"Roboto Condensed",Arial,sans-serif;font-weight:800;
  font-size:108px;color:var(--blue);line-height:1;margin-bottom:8px;letter-spacing:1px}
.why-cloth p{font-size:32px;line-height:1.25;margin-bottom:22px}
.savings{display:block;font-family:"Roboto Condensed",Arial,sans-serif;font-weight:800;
  font-size:60px;color:var(--green-head);line-height:1.15;margin-top:4px}
.hl{font-family:"Roboto Condensed",Arial,sans-serif;font-weight:700;color:var(--blue);font-size:38px}
.hl-big{font-family:"Roboto Condensed",Arial,sans-serif;font-weight:700;color:var(--blue);font-size:44px;line-height:1.15}
.why-cloth .easy{font-family:"Roboto Condensed",Arial,sans-serif;font-weight:700;font-size:40px;
  color:var(--green-head);line-height:1.2;margin-top:6px}
.contact{position:absolute;left:64px;top:2180px;width:1072px;display:flex;align-items:center;gap:22px;
  color:var(--white);font-size:30px;font-weight:700;white-space:nowrap}
.contact::before,.contact::after{content:"";flex:1;height:3px;background:var(--white);opacity:.7}
.brand-strip{position:absolute;left:40px;top:2260px;width:1120px;height:400px;background:var(--white);
  display:grid;grid-template-columns:repeat(3,1fr);grid-template-rows:1fr 1fr;align-items:center;justify-items:center;
  padding:20px 30px;border-radius:4px}
.partner{font-family:"Roboto Condensed",Arial,sans-serif;font-weight:700;font-size:48px;color:var(--leaf-deep)}
</style>
</head>
<body>
<main class="rack-card">
  <svg class="backdrop" viewBox="0 0 1200 2696" aria-hidden="true">
    <rect x="0" y="0" width="1200" height="360" fill="#ffffff"/>
    <path d="M1200 1500 C900 1800 600 1980 0 2060 L0 2696 L1200 2696Z" fill="#bfe09a"/>
    <path d="M1200 1680 C950 1950 600 2090 0 2130 L0 2696 L1200 2696Z" fill="#7cbf3a"/>
    <path d="M1200 1880 C950 2060 700 2140 0 2160 L0 2696 L1200 2696Z" fill="#3f8f2a"/>
  </svg>

  <header class="brand-header">
    <div class="brand-name"><span class="brand-dot"></span>Tiny Sprout</div>
    <div class="brand-tag">NATURAL BABY PRODUCTS</div>
  </header>

  <section class="why-cloth">
    <h1>WHY CLOTH?</h1>
    <p>I initially started doing my research on cloth diapers when I was pregnant with our first son. After realizing that I could
      <span class="savings">SAVE BETWEEN $500-$2000</span>
      (depending on the type of diaper used) <b>per child</b> if I cloth diapered, the decision was a no brainer to me... Upon researching the cost benefits of cloth diapering, I made some other helpful discoveries that made me a cloth diaper fanatic!</p>
    <p>-Disposable diapers are so wasteful. They make up over 30% of what is in our landfills today. And all of those diapers can take as long as <span class="hl">500 years to decompose</span>. Your cute little baby will go through <span class="hl">over a ton of disposable diapers</span> by the time they are ready to potty train!</p>
    <p>-Disposable diapers <span class="hl">contain a chemical called Dioxin</span>, which is extremely toxic and <span class="hl">cancer causing</span>, as reported by the EPA. Its been banned in most other countries.</p>
    <p>-Disposable diapers can actually cause diaper rash. The chemicals used by diaper manufacturers to make them absorbent of moisture are extremely harsh on your baby sensitive skin!</p>
    <p>-The gel used to absorb moisture in disposables called sodium polyacrylate (formerly also used in tampons) <span class="hl">encourages the growth of toxin producing bacteria.</span> Sodium polyacrylate was banned for use in tampons because it caused <span class="hl">toxic shock syndrome.</span></p>
    <p><span class="hl-big">-Disposable diapers have been linked to infertility later in life for men.</span> In May, 2000, a pediatric journal published a study which showed that scrotal <span class="hl">temperature in boys is increased</span> while wearing diapers and that prolonged disposable diaper use can completely destroy the physiological cooling mechanism important for sperm production.</p>
    <p class="easy">Modern cloth is easy – no more safety pins or rubber pants!</p>
  </section>

  <div class="contact">www.tinysproutnestling.example · molly@tinysproutnestling.example</div>

  <footer class="brand-strip">
    <span class="partner">Leafhop</span>
    <span class="partner">Meadow Rinse</span>
    <span class="partner">Softbough</span>
    <span class="partner">Hopwrap</span>
    <span class="partner">Willowmoon Organics</span>
  </footer>
</main>
</body>
</html>
```